BUSINESS CARD DESIGN

NAME- DALE VORSKIN
PHONE NUMER - 555- 714-9082
EMAIL- OFFICE@TRV-GROUNDMAKRZ.COM
BACK OF CARD- SPEACIALIZES IN LAND CLEARING, FORESTRY MUCLHING AND EXCAVATION

Contact Information for Business Card

NAME- DALE VORSKIN PHONE NUMER - 555- 714-9082 EMAIL- OFFICE@TRV-GROUNDMAKRZ.COM BACK OF CARD- SPEACIALIZES IN LAND CLEARING , MUCLHING AND EXCAVATION

```html
<!DOCTYPE html>
<html lang="en">
<head>
<meta charset="utf-8">
<title>Terravale Groundmakrz – Business Card</title>
<link href="https://fonts.googleapis.com/css2?family=Roboto:wght@300;400;700&display=swap" rel="stylesheet">
<style>
  :root {
    --bg: #e3e7e8;
    --card: #1f1f21;
    --card-deep: #0f0f10;
    --pattern: #161617;
    --gold: #f4b01b;
    --ink-light: #f1ede4;
  }
  * { margin: 0; padding: 0; box-sizing: border-box; }
  html, body {
    width: 1200px; height: 960px; overflow: hidden;
    background: var(--bg);
    font-family: "Roboto", Arial, sans-serif;
  }
  .card {
    position: absolute;
    left: 247px;
    width: 706px;
    height: 403px;
    background: var(--card);
    overflow: hidden;
  }
  .card--front { top: 58px; }
  .card--back { top: 499px; }

  .front-texture {
    position: absolute; inset: 0;
    background: radial-gradient(circle at 50% 50%, #242426 0%, var(--pattern) 100%);
  }
  .brand-lockup {
    position: absolute;
    left: 0; right: 0;
    display: flex; flex-direction: column; align-items: center;
    color: var(--gold);
  }
  .card--front .brand-lockup { top: 116px; }
  .brand-mark {
    width: 74px; height: 74px;
    border-radius: 50%;
    background: var(--gold);
    margin-bottom: 16px;
  }
  .brand-name {
    font-weight: 700;
    font-size: 17px;
    letter-spacing: 1.5px;
    text-align: center;
    line-height: 1.2;
  }
  .brand-phone {
    font-weight: 700;
    font-size: 10px;
    letter-spacing: 7px;
    margin-top: 8px;
  }
  .tagline {
    position: absolute;
    top: 362px; left: 0; right: 0;
    text-align: center;
    color: var(--gold);
    font-size: 15.5px;
    font-weight: 400;
    letter-spacing: 0.3px;
  }

  .back-shade { position: absolute; inset: 0; }
  .card--back .brand-lockup {
    top: 28px; left: 26px; right: auto; width: 210px;
  }
  .card--back .brand-mark { width: 100px; height: 100px; margin-bottom: 14px; }
  .card--back .brand-name { font-size: 16.5px; }

  .holder {
    position: absolute;
    right: 32px; top: 212px;
    font-size: 40px;
    letter-spacing: 1.5px;
    line-height: 44px;
  }
  .holder__first { color: var(--gold); font-weight: 700; }
  .holder__last { color: var(--ink-light); font-weight: 300; }
  .holder-bar {
    position: absolute;
    right: 0; top: 218px;
    width: 18px; height: 32px;
    background: var(--gold);
  }
  .contact {
    position: absolute;
    right: 24px; top: 309px;
    list-style: none;
  }
  .contact li {
    display: flex; align-items: center; justify-content: flex-end;
    height: 23.5px;
    color: var(--ink-light);
    font-size: 15.5px;
    font-weight: 400;
    letter-spacing: 0.8px;
  }
  .contact svg { width: 15px; height: 15px; margin-left: 7px; flex: none; }
</style>
</head>
<body>

<section class="card card--front">
  <div class="front-texture" role="img" aria-label="Embossed repeating brand pattern in dark charcoal"></div>
  <div class="brand-lockup">
    <div class="brand-mark"></div>
    <div class="brand-name">TERRAVALE<br>GROUNDMAKRZ LLC</div>
    <div class="brand-phone">555-714-9082</div>
  </div>
  <p class="tagline">SPEACIALIZES IN LAND CLEARING , MUCLHING AND EXCAVATION</p>
</section>

<section class="card card--back">
  <svg class="back-shade" viewBox="0 0 706 403" preserveAspectRatio="none" aria-hidden="true">
    <defs>
      <linearGradient id="foldShade" x1="0" y1="0" x2="0.15" y2="1">
        <stop offset="0" stop-color="#1f1f21"/>
        <stop offset="0.7" stop-color="#1a1a1c"/>
        <stop offset="1" stop-color="#0d0d0e"/>
      </linearGradient>
      <linearGradient id="edgeShadow" x1="0.5" y1="0" x2="0.42" y2="0.16">
        <stop offset="0" stop-color="#000" stop-opacity="0.55"/>
        <stop offset="1" stop-color="#000" stop-opacity="0"/>
      </linearGradient>
    </defs>
    <rect width="706" height="403" fill="var(--card)"/>
    <polygon points="0,0 680,0 680,22 28,380 0,403" fill="url(#foldShade)"/>
    <polygon points="680,22 28,380 60,380 690,40" fill="#000" opacity="0.35"/>
  </svg>

  <div class="brand-lockup">
    <div class="brand-mark"></div>
    <div class="brand-name">TERRAVALE<br>GROUNDMAKRZ LLC</div>
    <div class="brand-phone">555-714-9082</div>
  </div>

  <h1 class="holder"><span class="holder__first">DALE</span> <span class="holder__last">VORSKIN</span></h1>
  <div class="holder-bar"></div>

  <ul class="contact">
    <li>555- 714-9082
      <svg viewBox="0 0 24 24" aria-hidden="true"><path fill="#f4b01b" d="M6.6 10.8a15.1 15.1 0 0 0 6.6 6.6l2.2-2.2a1 1 0 0 1 1-.25 11.4 11.4 0 0 0 3.6.57 1 1 0 0 1 1 1V20a1 1 0 0 1-1 1A17 17 0 0 1 3 4a1 1 0 0 1 1-1h3.5a1 1 0 0 1 1 1c0 1.25.2 2.45.57 3.57a1 1 0 0 1-.25 1z"/></svg>
    </li>
    <li>WWW.TRV-GROUNDMAKRZ.COM
      <svg viewBox="0 0 24 24" aria-hidden="true"><circle cx="12" cy="12" r="10" fill="#f4b01b"/><path d="M2 12h20M12 2c3 3 3 17 0 20M12 2c-3 3-3 17 0 20" stroke="#1f1f21" stroke-width="1.4" fill="none"/></svg>
    </li>
    <li>OFFICE@TRV-GROUNDMAKRZ.COM
      <svg viewBox="0 0 24 24" aria-hidden="true"><rect x="2" y="6" width="20" height="14" rx="1.5" fill="#f4b01b"/><path d="M2 7l10 7 10-7" stroke="#1f1f21" stroke-width="1.6" fill="none"/></svg>
    </li>
  </ul>
</section>

</body>
</html>
```